MRT Property - Business Cards

Looking for a business card & general letterhead, signage etc design for our new logo.

Colours:
000a20
0056a2
00b5ef
0088ce
68cef2

Fonts:
Poppins
Karla

Please keep look and feel of new brand - example in the zip package I sent.

```html
<!DOCTYPE html>
<html lang="en">
<head>
<meta charset="utf-8">
<title>MRT Property – Business Cards</title>
<link rel="stylesheet" href="https://fonts.googleapis.com/css2?family=Poppins:wght@400;500;600;700&display=swap">
<style>
  :root {
    --ink: #000a20;
    --brand-blue: #0056a2;
    --bright-blue: #00b5ef;
    --mid-blue: #0088ce;
    --sky-blue: #68cef2;
    --card-white: #ffffff;
    --backdrop: #9a9a9a;
    --divider: #b9bcc2;
  }
  * { margin: 0; padding: 0; box-sizing: border-box; }
  html, body {
    width: 1093px; height: 1200px; overflow: hidden;
    background: var(--backdrop);
    font-family: "Poppins", sans-serif;
  }
  .canvas { position: relative; width: 1093px; height: 1200px; }

  .card {
    position: absolute; left: 265px; width: 578px; height: 356px;
    border-radius: 27px; overflow: hidden;
  }
  .card-front { top: 226px; background: var(--card-white); }
  .card-back { top: 621px; background: var(--brand-blue); }

  .footer-band {
    position: absolute; left: 0; bottom: 0; width: 578px; height: 52px;
    background: linear-gradient(180deg, var(--mid-blue) 0%, var(--brand-blue) 100%);
  }

  .wordmark {
    position: absolute; display: flex; align-items: center;
    font-weight: 600; white-space: nowrap; letter-spacing: 0.5px;
  }
  .wordmark-front {
    left: 36px; top: 158px; font-size: 28px; color: var(--brand-blue); gap: 10px;
  }
  .wordmark-back {
    left: 0; width: 578px; top: 122px; justify-content: center;
    font-size: 56px; color: var(--mid-blue); gap: 16px;
  }
  .wordmark-dot { border-radius: 50%; background: var(--bright-blue); flex: none; }
  .wordmark-front .wordmark-dot { width: 22px; height: 22px; }
  .wordmark-back .wordmark-dot { width: 40px; height: 40px; background: var(--sky-blue); }

  .divider {
    position: absolute; left: 288px; top: 74px; width: 1px; height: 209px;
    background: var(--divider);
  }

  .person { position: absolute; left: 311px; top: 89px; }
  .person-name {
    font-size: 23px; font-weight: 600; color: var(--brand-blue);
    line-height: 28px; letter-spacing: 0.2px;
  }
  .person-role { font-size: 17px; color: var(--ink); line-height: 18px; }

  .contact-list { position: absolute; left: 311px; top: 146px; list-style: none; }
  .contact-item {
    display: flex; align-items: center; gap: 7px;
    font-size: 17.5px; color: var(--ink); line-height: 21px;
  }
  .contact-icon { width: 15px; height: 15px; flex: none; }
  .web-name { color: var(--brand-blue); }

  .address {
    position: absolute; left: 312px; top: 220px;
    font-size: 17.5px; color: var(--ink); line-height: 21px; font-style: normal;
  }
</style>
</head>
<body>
<main class="canvas">

  <section class="card card-front" aria-label="Business card front">
    <div class="footer-band" role="img" aria-label="Decorative blue band along the bottom edge"></div>

    <div class="wordmark wordmark-front">
      <span class="wordmark-dot"></span>
      <span>MRT Property</span>
    </div>

    <div class="divider"></div>

    <div class="person">
      <h1 class="person-name">DANIEL HARTLEY</h1>
      <p class="person-role">Managing Director</p>
    </div>

    <ul class="contact-list">
      <li class="contact-item">
        <svg class="contact-icon" viewBox="0 0 16 16" aria-hidden="true">
          <path fill="none" stroke="var(--brand-blue)" stroke-width="1.8" stroke-linejoin="round" d="M3 1.5 L6 1.5 L7 5 L5.2 6.3 C6 8.2 7.8 10 9.7 10.8 L11 9 L14.5 10 L14.5 13 C14.5 14 13.6 14.6 12.6 14.5 C6.8 13.9 2.1 9.2 1.5 3.4 C1.4 2.4 2 1.5 3 1.5 Z"/>
          <path fill="none" stroke="var(--brand-blue)" stroke-width="1.4" stroke-linecap="round" d="M9.5 1.8 A5 5 0 0 1 14.2 6.5 M9.3 4.3 A2.5 2.5 0 0 1 11.7 6.7"/>
        </svg>
        <span>044-987 650 321</span>
      </li>
      <li class="contact-item">
        <svg class="contact-icon" viewBox="0 0 16 16" aria-hidden="true">
          <rect x="0.5" y="3" width="15" height="10" fill="var(--brand-blue)"/>
          <path fill="none" stroke="var(--card-white)" stroke-width="1.2" d="M0.8 3.5 L8 9 L15.2 3.5 M0.8 12.6 L5.8 7.4 M15.2 12.6 L10.2 7.4"/>
        </svg>
        <span>hello@mrtprop.com</span>
      </li>
      <li class="contact-item">
        <svg class="contact-icon" viewBox="0 0 16 16" aria-hidden="true">
          <g fill="none" stroke="var(--brand-blue)" stroke-width="1.3">
            <circle cx="8" cy="8" r="6.9"/>
            <ellipse cx="8" cy="8" rx="3" ry="6.9"/>
            <path d="M1.1 8 H14.9 M2.2 4.5 H13.8 M2.2 11.5 H13.8 M8 1.1 V14.9"/>
          </g>
        </svg>
        <span>www.<span class="web-name">mrtproperty</span>.com</span>
      </li>
    </ul>

    <address class="address">
      18 Harbour Road, Suite 4<br>
      20451, Westland
    </address>
  </section>

  <section class="card card-back" aria-label="Business card back">
    <div class="wordmark wordmark-back">
      <span class="wordmark-dot"></span>
      <span>MRT Property</span>
    </div>
  </section>

</main>
</body>
</html>
```